Mortgage Broking Flyer to attract attention

We are looking for double sided, colour DL sized flyers for a mail drop to inform people what services we offer.
We are a Mortgage Broking Business in Alice Springs NT Australia. Alice Springs is a large country town so we want something that is personal, a little bit playful but still professional, and is going to capture the attention of potential clients when they first look at it so they want to read on.
Please use our logo and colours (red & white) plus a photo of our team – all attached.
Brochure Front: IMPORTANT
Please come up with a tag line based on the following-We want to be seen as different to the bank, more friendly, personable, we listen, want to help and want people to keep coming back even for the little things.
The home page from our website has good dot points but we would like them shorter and to the point www.ochrecrestlending.com.au
Plus include something which lets customer know that we can assist purchases made through any real estate office, anywhere in Australia
Don’t want the front to contain too many long sentences or paragraphs.
Brochure Back:
Please include:
Services/Specialties
• First home buyers
• Refinancing
• Investments
• Construction loans
• Debt consolidation
• Commercial finance
Please include the following contact details:
Dominic Farrow – Managing Director
Prudence Wexley – Loans Consultant
Maeve Dunleavy – Loans Consultant
Suite 4/17 Corbel Street, Alice Springs NT 0870
Phone: 08 8961 4728
www.ochrecrestlending.com.au
We must include the following fine print at the back/bottom of the brochure:
Dominic Farrow (Credit Representative Number: 527814), Prudence Wexley (Credit Representative Number: 527813) and Maeve Dunleavy (Credit Representative Number: 613290) are credit representatives of QMTRV Pty Ltd (Australian Credit Licence Number: 458906)
Please feel free to email me with any questions.
maeve@ochrecrestlending.com.au

```html
<!DOCTYPE html>
<html lang="en">
<head>
<meta charset="utf-8">
<title>Ochre Crest Lending – DL Flyer</title>
<link rel="stylesheet" href="https://fonts.googleapis.com/css2?family=Montserrat:wght@400;600;700&family=Roboto+Condensed:ital,wght@0,300;0,400;0,700;1,400;1,700&display=swap">
<style>
  :root {
    --red: #d81f26;
    --red-deep: #b5151c;
    --cream: #f3f0ea;
    --blush: #f1dcdc;
    --white: #ffffff;
    --stage: #e6e6e8;
  }
  * { margin: 0; padding: 0; box-sizing: border-box; }
  html, body { width: 1200px; height: 1000px; overflow: hidden; background: var(--stage); }
  .canvas { position: relative; width: 1200px; height: 1000px; }

  .flyer { position: absolute; top: 110px; width: 450px; height: 780px; overflow: hidden;
           box-shadow: 0 6px 18px rgba(0,0,0,.18); }
  .flyer-front { left: 90px; background: var(--cream); }
  .flyer-back { left: 660px; background: var(--red); }
  .flyer-shapes { position: absolute; inset: 0; }

  /* Front */
  .brand { position: absolute; top: 22px; left: 26px; display: flex; align-items: center; gap: 16px; }
  .brand-dot { width: 54px; height: 54px; border-radius: 50%; background: var(--white); }
  .brand-name { font-family: "Roboto Condensed", sans-serif; font-weight: 300; font-size: 31px;
                color: var(--white); letter-spacing: .5px; text-transform: uppercase; }
  .tagline { position: absolute; top: 118px; left: 258px; font-family: "Montserrat", sans-serif;
             font-weight: 700; font-size: 18px; line-height: 22px; color: var(--white); text-transform: uppercase; }
  .tagline span { display: block; }
  .tagline span:nth-child(2) { margin-left: -4px; }
  .tagline span:nth-child(3) { margin-left: -6px; }

  .promise-list { position: absolute; top: 372px; left: 50px; list-style: none;
                  font-family: "Roboto Condensed", sans-serif; font-style: italic; color: var(--red);
                  font-size: 25px; text-transform: uppercase; }
  .promise-list li { height: 37px; }
  .promise-list b { font-weight: 700; margin-right: 8px; }

  .reach { position: absolute; top: 620px; left: 28px; font-family: "Roboto Condensed", sans-serif;
           font-style: italic; color: var(--white); font-size: 22px; line-height: 30px; letter-spacing: .3px; }
  .reach .big { font-size: 24px; }
  .reach strong { font-weight: 700; }

  /* Back */
  .services { position: absolute; top: 28px; left: 0; width: 150px; list-style: none; text-align: center;
              font-family: "Montserrat", sans-serif; font-weight: 700; font-size: 10.5px; line-height: 12px;
              color: var(--red); text-transform: uppercase; }
  .service { position: absolute; left: 0; width: 150px; display: flex; flex-direction: column; align-items: center; gap: 5px; }
  .service svg { width: 32px; height: 32px; }

  .team-photo { position: absolute; top: 462px; left: 28px; width: 178px; height: 84px; border-radius: 6px;
                background: linear-gradient(100deg, #6d7a55 0%, #a4a890 35%, #d9d3c6 55%, #3f4d7a 85%, #2f3b6a 100%); }

  .back-brand { position: absolute; top: 24px; left: 240px; display: flex; align-items: center; gap: 10px; }
  .back-brand .brand-dot { width: 44px; height: 44px; }
  .back-brand .brand-name { font-family: "Montserrat", sans-serif; font-weight: 600; font-size: 13px;
                            letter-spacing: 0; line-height: 15px; width: 90px; }

  .contact { position: absolute; left: 222px; top: 92px; font-family: "Montserrat", sans-serif;
             color: var(--white); font-size: 14px; line-height: 18px; }
  .contact address { font-style: normal; font-weight: 600; }
  .contact .phone { margin-top: 28px; margin-left: 8px; }
  .contact .label { font-weight: 400; }
  .contact .value { font-weight: 600; }
  .contact .web { margin-top: 26px; margin-left: 14px; font-weight: 600; }

  .team { position: absolute; top: 568px; left: 32px; list-style: none; font-family: "Montserrat", sans-serif; color: var(--white); }
  .team li { height: 59px; }
  .team .name { display: block; font-weight: 700; font-size: 20px; letter-spacing: .3px; text-transform: uppercase; }
  .team .role { display: block; font-size: 12.5px; margin-top: 1px; }
  .team li:nth-child(1) .role { padding-left: 124px; }
  .team li:nth-child(2) .role { padding-left: 162px; }
  .team li:nth-child(3) .role { padding-left: 98px; }

  .fine-print { position: absolute; left: 424px; top: 760px; width: 540px; transform: rotate(-90deg);
                transform-origin: top left; font-family: "Montserrat", sans-serif; font-size: 6.6px;
                line-height: 9px; color: rgba(255,255,255,.9); }
</style>
</head>
<body>
<main class="canvas">

  <!-- FRONT -->
  <section class="flyer flyer-front" aria-label="Flyer front">
    <svg class="flyer-shapes" viewBox="0 0 450 780" aria-hidden="true">
      <defs>
        <linearGradient id="heroTone" x1="0" y1="0" x2="1" y2="0">
          <stop offset="0" stop-color="#f4f1ef"/>
          <stop offset=".45" stop-color="#e4d5d4"/>
          <stop offset=".7" stop-color="#b8252d"/>
          <stop offset="1" stop-color="#7e1116"/>
        </linearGradient>
      </defs>
      <rect x="0" y="0" width="450" height="120" fill="var(--red)"/>
      <path d="M0 320 H450 V345 Q225 340 0 332 Z" fill="var(--blush)"/>
      <path d="M0 570 Q225 556 450 572 V640 H0 Z" fill="var(--blush)"/>
      <path d="M0 660 Q0 612 48 612 H450 V780 H0 Z" fill="var(--red)"/>
    </svg>
    <div role="img" aria-label="Photo of a smiling man holding a small model house"
         style="position:absolute;left:0;top:88px;width:450px;height:240px;background:linear-gradient(90deg,#f4f1ef 0%,#e6d8d6 42%,#b8252d 70%,#7e1116 100%);border-radius:60px 0 32px 0;"></div>

    <div class="brand">
      <span class="brand-dot"></span>
      <span class="brand-name">Ochre Crest Lending</span>
    </div>

    <h1 class="tagline"><span>We are</span><span>different</span><span>from banks</span></h1>

    <ol class="promise-list">
      <li><b>01.</b>We are friendly...</li>
      <li><b>02.</b>Personable...</li>
      <li><b>03.</b>We listen...</li>
      <li><b>04.</b>Want to help</li>
      <li><b>05.</b>Want you coming back...</li>
    </ol>

    <p class="reach">We can assist purchases made through<br>any real estate office,<br><span class="big">anywhere in <strong>Australia</strong></span></p>
  </section>

  <!-- BACK -->
  <section class="flyer flyer-back" aria-label="Flyer back">
    <div role="img" aria-label="Office desk photo in a red tint"
         style="position:absolute;inset:0;background:linear-gradient(160deg,#d81f26 0%,#cf2a30 45%,#e0474c 70%,#c41b22 100%);"></div>
    <svg class="flyer-shapes" viewBox="0 0 450 780" aria-hidden="true">
      <path d="M0 0 H118 L262 392 Q276 446 228 452 H0 Z" fill="var(--cream)"/>
    </svg>

    <ul class="services">
      <li class="service" style="top:0">
        <svg viewBox="0 0 32 32"><circle cx="16" cy="16" r="16" fill="var(--red)"/><rect x="10" y="9" width="12" height="14" fill="#fff"/><g fill="var(--red)"><rect x="12" y="11" width="2.5" height="2.5"/><rect x="17.5" y="11" width="2.5" height="2.5"/><rect x="12" y="15" width="2.5" height="2.5"/><rect x="17.5" y="15" width="2.5" height="2.5"/><rect x="14.5" y="19" width="3" height="4"/></g></svg>
        <span>First home<br>buyers</span>
      </li>
      <li class="service" style="top:60px">
        <svg viewBox="0 0 32 32"><circle cx="16" cy="16" r="16" fill="var(--red)"/><circle cx="12" cy="13" r="5" fill="#fff"/><circle cx="20" cy="19" r="5" fill="#fff"/></svg>
        <span>Refinancing</span>
      </li>
      <li class="service" style="top:126px">
        <svg viewBox="0 0 32 32"><circle cx="16" cy="16" r="16" fill="var(--red)"/><g fill="#fff"><rect x="9" y="18" width="3.5" height="5"/><rect x="14.2" y="14" width="3.5" height="9"/><rect x="19.4" y="10" width="3.5" height="13"/></g></svg>
        <span>Investments</span>
      </li>
      <li class="service" style="top:188px">
        <svg viewBox="0 0 32 32"><circle cx="16" cy="16" r="16" fill="var(--red)"/><g fill="#fff"><path d="M8 13 L16 8 L24 13 Z"/><rect x="10" y="14" width="2.5" height="7"/><rect x="14.8" y="14" width="2.5" height="7"/><rect x="19.5" y="14" width="2.5" height="7"/><rect x="8" y="22" width="16" height="2"/></g></svg>
        <span>Construction<br>loans</span>
      </li>
      <li class="service" style="top:268px">
        <svg viewBox="0 0 32 32"><circle cx="16" cy="16" r="16" fill="var(--red)"/><rect x="10" y="9" width="12" height="15" rx="1.5" fill="#fff"/><text x="16" y="21" text-anchor="middle" font-family="Montserrat, sans-serif" font-weight="700" font-size="11" fill="var(--red)">$</text></svg>
        <span>Debt<br>consolidation</span>
      </li>
      <li class="service" style="top:346px">
        <svg viewBox="0 0 32 32"><circle cx="16" cy="16" r="16" fill="var(--red)"/><g fill="#fff"><path d="M7 14 L13 11 L18 15 L15 18 Z"/><path d="M25 14 L19 11 L13 16 L17 21 Z"/></g></svg>
        <span>Commercial<br>finance</span>
      </li>
    </ul>

    <div class="team-photo" role="img" aria-label="Photo of the three-person lending team"></div>

    <div class="back-brand">
      <span class="brand-dot"></span>
      <span class="brand-name">Ochre Crest Lending</span>
    </div>

    <div class="contact">
      <address>Suite 4/17 Corbel<br>Street,<br>Alice Springs<br>NT 0870</address>
      <p class="phone"><span class="label">Phone</span><br><span class="value">08 8961 4728</span></p>
      <p class="web">www.<br>ochrecrestlending.<br>com.au</p>
    </div>

    <ul class="team">
      <li><span class="name">Dominic Farrow</span><span class="role">Managing Director</span></li>
      <li><span class="name">Prudence Wexley</span><span class="role">Loans Consultant</span></li>
      <li><span class="name">Maeve Dunleavy</span><span class="role">Loans Consultant</span></li>
    </ul>

    <p class="fine-print">Dominic Farrow (Credit Representative Number: 527814), Prudence Wexley (Credit Representative Number: 527813) and Maeve Dunleavy (Credit Representative Number: 613290) are credit representatives of QMTRV Pty Ltd (Australian Credit Licence Number: 458906)</p>
  </section>

</main>
</body>
</html>
```